Mental Health care Company in Washington DC

We are a new mental health care services provider in Washington DC. Please look at these sites.
https://brightwaterfamilysupport.com
https://www.quietharborinc.com
https://willowgate-dc.org/
https://www.tidepathdc.com
https://www.thelanternofdc.com

```html
<!DOCTYPE html>
<html lang="en">
<head>
<meta charset="utf-8">
<title>Kestrel Health Services — Compassionate Mental Health Care</title>
<link rel="stylesheet" href="https://fonts.googleapis.com/css2?family=Poppins:wght@400;500;600;700&display=swap">
<style>
:root{
  --navy:#0f1f3d;
  --navy-deep:#0c1a36;
  --orange:#f47f20;
  --teal:#a3d9dc;
  --text:#4a4f5c;
  --white:#ffffff;
}
*{box-sizing:border-box;margin:0;padding:0}
html,body{width:1200px;height:3071px;overflow:hidden;background:var(--white)}
body{font-family:"Poppins",sans-serif;color:var(--navy);position:relative}
.abs{position:absolute}

/* header */
.brand{left:101px;top:40px;font-size:30px;font-weight:600;color:var(--navy);line-height:1.1}
.brand small{display:block;font-size:13px;font-weight:600;letter-spacing:7px;margin-top:2px}
.nav{left:440px;top:48px;display:flex;gap:32px;font-size:16px;color:#3a3f4d}
.nav .active{color:var(--navy);font-weight:600}
.btn{background:var(--orange);color:var(--white);font-weight:700;font-size:15px;border-radius:30px;display:flex;align-items:center;justify-content:center}
.btn-header{left:863px;top:36px;width:236px;height:48px}

/* hero */
.hero-title{left:100px;top:168px;font-size:54px;line-height:57px;font-weight:700;letter-spacing:-.3px}
.hero-title span{font-weight:400;display:block}
.hero-text{left:100px;top:356px;width:480px;font-size:16.5px;line-height:29px;color:var(--text)}
.btn-hero{left:101px;top:467px;width:267px;height:49px}

.shape{position:absolute}
.photo-warm{background:linear-gradient(160deg,#cfc3b3,#8d8377 60%,#5e6470)}
.photo-soft{background:linear-gradient(150deg,#e8e2da,#b9ab9a 55%,#7c7b80)}
.photo-garden{background:linear-gradient(160deg,#b99a7c,#6f7a5c 55%,#3f5a33)}

/* services */
.services-bg{left:0;top:560px;width:1200px;height:762px}
.section-title{font-size:46px;font-weight:700;text-align:center;width:1200px;left:0}
.services-title{top:746px;color:var(--white)}
.card{position:absolute;width:238px;text-align:center;padding:40px 26px 0;color:var(--navy)}
.card h3{font-size:20px;font-weight:600;line-height:26px;margin:14px 0 18px}
.card p{font-size:15px;line-height:26px}
.card svg{width:62px;height:62px}
.card-teal{background:var(--teal)}
.card-orange{background:var(--orange);color:var(--white)}
.r-right{border-radius:119px 119px 119px 0}
.r-left{border-radius:119px 119px 0 119px}

/* about */
.about-title{left:628px;top:1444px;font-size:46px;font-weight:700}
.about-sub{left:628px;top:1527px;font-size:16.5px;font-weight:600}
.about-text{left:628px;top:1568px;width:465px;font-size:16px;line-height:29px;color:var(--text)}
.about-text p+p{margin-top:6px}
.about-text strong{color:var(--navy);font-weight:600}
.btn-about{left:628px;top:1860px;width:149px;height:48px}

/* why */
.why-title{top:2066px;color:var(--navy)}
.why-bg{left:0;top:2150px;width:1200px;height:620px;background:linear-gradient(180deg,#ffffff 0%,#ffffff 55%,#dff1f2 100%)}
.feature{position:absolute;width:300px;font-size:16px;line-height:26px;font-weight:500;color:#3a3f4d}
.feature.left{text-align:right}
.feature .icon{width:56px;height:52px;position:relative;display:inline-block;margin-bottom:6px}
.feature .icon i{position:absolute;width:36px;height:36px;border-radius:50%;left:0;top:12px}
.feature .icon svg{position:absolute;left:8px;top:0;width:44px;height:46px}

/* footer */
.footer-bg{left:0;top:2700px;width:1200px;height:371px}
.footer-brand{left:101px;top:2868px;font-size:44px;font-weight:600;color:var(--white);line-height:1.05}
.footer-brand small{display:block;font-size:19px;letter-spacing:9px;margin-top:4px}
.copyright{left:133px;top:2978px;font-size:15px;color:var(--white)}
.f-col{position:absolute;top:2884px;color:var(--white)}
.f-col h4{font-size:14px;font-weight:500;letter-spacing:1.5px;color:#b8c0d0;margin-bottom:18px}
.f-col p{font-size:15px;font-weight:600;line-height:26px}
</style>
</head>
<body>

<!-- header -->
<div class="abs brand">Kestrel Health<small>SERVICES</small></div>
<nav class="abs nav">
  <span class="active">Home</span><span>About</span><span>Services</span><span>Blog</span><span>Contact Us</span>
</nav>
<a class="abs btn btn-header">Make an Appointment</a>

<!-- hero -->
<h1 class="abs hero-title">Compassionate<br>Mental Health Care<span>for a Stronger You</span></h1>
<p class="abs hero-text">Supporting individuals and families with personalized, evidence-based mental health services designed to foster hope, healing, and lasting wellness.</p>
<a class="abs btn btn-hero">Schedule an Appointment</a>

<div class="shape" style="left:632px;top:152px;width:183px;height:260px;background:var(--teal);border-radius:92px 92px 0 0"></div>
<div class="shape" style="left:810px;top:392px;width:210px;height:184px;background:var(--orange);border-radius:0 0 105px 105px"></div>
<div class="shape photo-warm" role="img" aria-label="Smiling young girl seated on a sofa" style="left:632px;top:262px;width:183px;height:312px;border-radius:0 0 92px 92px"></div>
<div class="shape photo-soft" role="img" aria-label="Therapist taking notes while talking with a child" style="left:826px;top:125px;width:274px;height:382px;border-radius:137px 137px 0 0"></div>
<div class="shape" style="left:815px;top:268px;width:11px;height:200px;background:var(--orange)"></div>

<!-- services -->
<svg class="abs services-bg" viewBox="0 0 1200 762" preserveAspectRatio="none" role="img" aria-label="Dimmed background of a therapy session with puzzle pieces">
  <defs>
    <linearGradient id="svcGrad" x1="0" y1="0" x2="1" y2="1">
      <stop offset="0" stop-color="#1a2d4f"/><stop offset=".5" stop-color="#16284a"/><stop offset="1" stop-color="#0f1f3d"/>
    </linearGradient>
  </defs>
  <path d="M0 10 Q600 170 1200 10 L1200 762 L0 762 Z" fill="url(#svcGrad)"/>
</svg>
<h2 class="abs section-title services-title">Our Services</h2>

<div class="card card-teal r-right" style="left:99px;top:810px;height:346px">
  <svg viewBox="0 0 62 62" fill="none" stroke="#0f1f3d" stroke-width="2.2" stroke-linecap="round" stroke-linejoin="round"><circle cx="31" cy="20" r="12"/><path d="M31 14v12M25 20h12"/><path d="M8 30l8 14 10 6v8M54 30l-8 14-10 6v8M24 58h14"/></svg>
  <h3>Medical<br>Services</h3>
  <p>Lorem ipsum dolor sit amet, consectetur adipi scing elit, sed do eius mod tempor incidid.</p>
</div>
<div class="card card-orange r-right" style="left:354px;top:858px;height:347px">
  <svg viewBox="0 0 62 62" fill="none" stroke="#ffffff" stroke-width="2.2" stroke-linecap="round" stroke-linejoin="round"><path d="M18 56V44c-6-4-9-10-9-17C9 15 19 6 31 6s21 9 21 20l5 10h-5v8c0 3-2 5-5 5h-5v7"/><path d="M22 18v20M31 16v22M40 18v20"/><circle cx="22" cy="24" r="2.5"/><circle cx="31" cy="31" r="2.5"/><circle cx="40" cy="22" r="2.5"/></svg>
  <h3>Behavioral<br>Health</h3>
  <p>Lorem ipsum dolor sit amet, consectetur adipi scing elit, sed do eius mod tempor incidid.</p>
  <svg viewBox="0 0 40 12" style="width:36px;height:12px;margin-top:12px" fill="none" stroke="#fff" stroke-width="1.6" stroke-linecap="round"><path d="M2 6h35M31 1l6 5-6 5"/></svg>
</div>
<div class="card card-teal r-left" style="left:608px;top:858px;height:347px">
  <svg viewBox="0 0 62 62" fill="none" stroke="#0f1f3d" stroke-width="2.2" stroke-linecap="round" stroke-linejoin="round"><circle cx="31" cy="12" r="5"/><circle cx="14" cy="14" r="4.5"/><circle cx="48" cy="14" r="4.5"/><path d="M22 30c0-6 4-10 9-10s9 4 9 10M6 30c0-5 4-8 8-8 2 0 4 1 5 2M56 30c0-5-4-8-8-8-2 0-4 1-5 2"/><circle cx="31" cy="44" r="12"/><path d="M25 44l4 4 8-8"/></svg>
  <h3>Human<br>Services</h3>
  <p>Lorem ipsum dolor sit amet, consectetur adipi scing elit, sed do eius mod tempor incidid.</p>
</div>
<div class="card card-teal r-left" style="left:863px;top:810px;height:346px">
  <svg viewBox="0 0 62 62" fill="none" stroke="#0f1f3d" stroke-width="2.2" stroke-linecap="round" stroke-linejoin="round"><path d="M18 56V44c-6-4-9-10-9-17C9 15 19 6 31 6s21 9 21 20l5 10h-5v8c0 3-2 5-5 5h-5v7"/><circle cx="30" cy="24" r="10"/><rect x="23" y="20" width="14" height="8" rx="4" transform="rotate(-35 30 24)"/></svg>
  <h3>Substance<br>Abuse/Addiction</h3>
  <p>Lorem ipsum dolor sit amet, consectetur adipi scing elit, sed do eius mod tempor incidid.</p>
</div>

<!-- about -->
<div class="shape" style="left:365px;top:1477px;width:183px;height:250px;background:var(--teal);border-radius:92px 92px 0 0"></div>
<div class="shape" style="left:128px;top:1800px;width:262px;height:155px;background:var(--orange);border-radius:0 0 131px 131px"></div>
<div class="shape photo-garden" role="img" aria-label="Older woman tending plants in a community garden" style="left:99px;top:1472px;width:282px;height:383px;border-radius:141px 141px 0 0"></div>
<div class="shape photo-garden" role="img" aria-label="Younger woman holding dried plant stems in the garden" style="left:382px;top:1555px;width:184px;height:405px;border-radius:0 0 92px 92px;background:linear-gradient(170deg,#a58670,#6b6a52 50%,#44633a)"></div>

<h2 class="abs about-title">About Us</h2>
<p class="abs about-sub">Dedicated to Your Mental Well-Being</p>
<div class="abs about-text" style="top:1568px">
  <p>We are a trusted mental health care provider proudly serving the Washington, DC community. Our mission is to deliver compassionate, accessible, and culturally sensitive services that empower individuals to thrive emotionally, mentally, and socially.</p>
  <p>At the heart of our practice is a belief in the dignity, worth, and potential of every person we serve. Whether you’re seeking support for yourself, a loved one, or a community partner — <strong>we’re here to help.</strong></p>
</div>
<a class="abs btn btn-about">Read More</a>

<!-- why choose us -->
<div class="abs why-bg"></div>
<h2 class="abs section-title why-title">Why Choose Us</h2>

<div class="shape photo-soft" role="img" aria-label="Hands holding a smiling stress ball" style="left:548px;top:2196px;width:105px;height:190px;border-radius:52px 52px 0 0;border-bottom:8px solid var(--teal)"></div>
<div class="shape" role="img" aria-label="Hands resting together in support" style="left:548px;top:2392px;width:105px;height:92px;background:linear-gradient(160deg,#c9a386,#8a5a44)"></div>
<div class="shape photo-warm" role="img" aria-label="Hands protecting paper cut-out family figures" style="left:548px;top:2490px;width:105px;height:185px;border-radius:0 0 52px 52px;border-bottom:8px solid var(--orange);background:linear-gradient(170deg,#dcb8a4,#a57763)"></div>

<div class="feature left" style="left:179px;top:2234px">
  <span class="icon"><i style="background:var(--teal);left:14px"></i><svg viewBox="0 0 44 46" fill="none" stroke="#0f1f3d" stroke-width="2" stroke-linecap="round"><circle cx="22" cy="8" r="5"/><path d="M14 24c0-5 4-9 8-9s8 4 8 9v8H14z M4 20l6 14 8 4v6M40 20l-6 14-8 4v6"/></svg></span><br>
  Individualized, person-centered care plans
</div>
<div class="feature" style="left:721px;top:2234px">
  <span class="icon"><i style="background:var(--teal);left:14px"></i><svg viewBox="0 0 44 46" fill="none" stroke="#0f1f3d" stroke-width="2" stroke-linecap="round" style="left:0"><rect x="2" y="2" width="38" height="28" rx="2"/><path d="M9 10h24M9 16h16"/><circle cx="21" cy="32" r="6"/><path d="M17 37l-2 8 6-3 6 3-2-8"/></svg></span><br>
  Compassionate, licensed mental health professionals
</div>
<div class="feature left" style="left:179px;top:2514px">
  <span class="icon"><i style="background:#fbc9a0;left:14px"></i><svg viewBox="0 0 44 46" fill="none" stroke="#0f1f3d" stroke-width="2" stroke-linecap="round"><path d="M22 42C8 32 2 24 2 15 2 8 7 3 13 3c4 0 7 2 9 5 2-3 5-5 9-5 6 0 11 5 11 12 0 9-6 17-20 27z"/><circle cx="15" cy="18" r="3"/><circle cx="29" cy="18" r="3"/><path d="M10 28c1-4 3-5 5-5s4 1 5 5M24 28c1-4 3-5 5-5s4 1 5 5"/></svg></span><br>
  Focus on community connection and advocacy
</div>
<div class="feature" style="left:721px;top:2514px">
  <span class="icon"><i style="background:#fbc9a0;left:22px"></i><svg viewBox="0 0 44 46" fill="none" stroke="#0f1f3d" stroke-width="2" stroke-linecap="round" style="left:0"><path d="M4 30l10-14 8 6 8-6 10 14-12 12-6-6-6 6z"/><path d="M16 4l2 5M24 2v5M32 4l-2 5"/></svg></span><br>
  Safe, supportive, and confidential environment
</div>

<!-- footer -->
<svg class="abs footer-bg" viewBox="0 0 1200 371" preserveAspectRatio="none" aria-hidden="true">
  <path d="M0 22 Q600 110 1200 22 L1200 371 L0 371 Z" fill="var(--navy-deep)"/>
</svg>
<div class="abs footer-brand">Kestrel Health<small>SERVICES</small></div>
<p class="abs copyright">2025 All Rights Reserved.</p>
<div class="f-col" style="left:430px">
  <h4>OUR LOCATION</h4>
  <p>880 Larkspur Street NW,<br>Suite 210, Washington, DC<br>20009</p>
</div>
<div class="f-col" style="left:686px">
  <h4>CONTACT US</h4>
  <p>(202) 555-0147<br>hello@kestrelhealthservices.com</p>
</div>
<div class="f-col" style="left:956px">
  <h4>QUICK LINKS</h4>
  <p>Home<br>About<br>Services<br>Blog</p>
</div>

</body>
</html>
```